Broschüre für Personaldienstleister
Zielgruppe
Wir sind ein Personaldienstleister und vermitteln ausländisches medizinisches Fachpersonal an deutsche Einrichtungen. Unsere Zielgruppe sind Krankenhäuser, Pflegeheime, Ärztehäuser, Praxen, Labore und weitere medizinische Institutionen.
Aufgabenstellung
Wir haben eine Infobroschüre sowie eine PowerPoint Präsentation bereits mit einem groben Design erstellt. Texte und Beispielbilder (Stockmaterial) sind ebenfalls vorhanden, gerne wünschen wir uns auch Eigeninitiative bei der Wahl der Bilder passend zum neuen Design.
Wir wünschen uns ein Redesign mit einem kreativen, einzigartigen Design. Zudem ist uns wichtig, dass unsere Infografiken qualitativ und hochwertig gestaltet werden.
Dieses Projekt ist mit zukünftigen Folgeprojekten verbunden, da wir weitere Präsentationen und Broschüren für andere Zielgruppen benötigen.

```html
<!DOCTYPE html>
<html lang="de">
<head>
<meta charset="utf-8">
<title>Veridan HR – Broschüre</title>
<link href="https://fonts.googleapis.com/css2?family=Montserrat:wght@600;700;800&family=Roboto:wght@400;500;700&display=swap" rel="stylesheet">
<style>
:root{
  --bg:#e4e6e5;
  --paper:#f4f5f4;
  --teal-dark:#1d4a48;
  --teal:#2f7b69;
  --teal-mid:#4f9580;
  --teal-soft:#a9cfc0;
  --teal-faint:#d5e7df;
  --accent:#3c9c80;
  --ink:#1f3a38;
  --text:#35504d;
  --white:#ffffff;
}
*{box-sizing:border-box;margin:0;padding:0}
html,body{width:1200px;height:830px;overflow:hidden;background:var(--bg)}
body{font-family:"Roboto",Arial,sans-serif;color:var(--text);position:relative}
.page{position:absolute;top:10px;width:573px;height:810px;background:var(--paper);overflow:hidden;box-shadow:0 4px 18px rgba(0,0,0,.12)}
.page--left{left:27px}
.page--right{left:600px}
.page--right::before{content:"";position:absolute;left:0;top:0;bottom:0;width:26px;background:linear-gradient(90deg,rgba(0,0,0,.08),rgba(0,0,0,0))}

/* left page */
.hero-photo{position:absolute;left:0;top:0;width:100%;height:320px;background:linear-gradient(160deg,#c9d3d2 0%,#eef1f0 40%,#b9c6c4 75%,#8ea3a0 100%)}
.title-band{position:absolute;left:0;top:290px;width:100%;height:130px;background:var(--teal-dark);clip-path:polygon(0 20%,100% 0,100% 100%,0 100%);padding:44px 26px 0}
.title-band h1{font-family:"Montserrat",Arial,sans-serif;font-weight:700;font-size:18px;line-height:1.2;color:var(--white);white-space:nowrap}
.title-band h2{font-family:"Montserrat",Arial,sans-serif;font-weight:600;font-size:20px;line-height:1.2;color:var(--accent);margin-top:6px;padding-left:60px;white-space:nowrap}

.hub{position:absolute;left:0;top:0;width:100%;height:100%;pointer-events:none}
.hub-core{position:absolute;left:240px;top:545px;width:100px;height:100px;border-radius:50%;background:var(--teal-dark);display:flex;align-items:center;justify-content:center;font-weight:700;font-size:15px;color:var(--white)}

.pill{position:absolute;width:218px;height:72px;border-radius:36px;display:flex;align-items:center;padding:0 14px;gap:10px}
.pill__icon{flex:0 0 50px;height:50px;border-radius:50%;background:var(--white);display:flex;align-items:center;justify-content:center}
.pill__body h3{font-size:10.5px;font-weight:500;color:var(--white);margin-bottom:3px}
.pill__body p{font-size:8px;line-height:1.25;color:var(--white)}
.pill--left{flex-direction:row-reverse}
.pill--dark{background:var(--teal-dark)}
.pill--mid{background:var(--teal-mid)}
.pill--faint{background:var(--teal-faint)}
.pill--faint .pill__body h3,.pill--faint .pill__body p{color:#a9c8bc}
.pill--faint .pill__icon{background:#eef5f2}

.footer{position:absolute;left:0;bottom:0;width:100%;height:38px;background:var(--teal);display:flex;align-items:center;justify-content:space-around;padding:0 70px 0 10px;font-size:10px;color:var(--white);letter-spacing:.3px;white-space:nowrap}
.footer::after{content:"";position:absolute;right:0;top:0;width:60px;height:100%;background:var(--teal-dark)}

/* right page */
.benefits-title{position:absolute;left:40px;top:34px;width:500px;font-family:"Montserrat",Arial,sans-serif;font-weight:700;font-size:20px;line-height:1.25;color:var(--ink)}
.brand-hex{position:absolute;left:195px;top:300px;width:190px;height:200px}
.brand-name{position:absolute;left:195px;top:386px;width:190px;text-align:center;font-family:"Montserrat",Arial,sans-serif;font-weight:800;font-size:19px;color:var(--teal-dark)}

.benefit{position:absolute;width:182px;border:1.5px dashed #9aaaa7;border-radius:22px;padding:14px 14px 12px 22px}
.benefit h4{font-size:9.5px;font-weight:700;color:var(--ink);margin-bottom:4px}
.benefit p{font-size:8.3px;line-height:1.3;color:var(--text)}
.benefit__hex{position:absolute;width:34px;height:38px}
.benefit--l .benefit__hex{left:-18px;top:50%;margin-top:-19px}
.benefit--r .benefit__hex{right:-18px;top:50%;margin-top:-19px}
.benefit--t .benefit__hex{left:50%;margin-left:-17px;top:-20px}
</style>
</head>
<body>

<section class="page page--left">
  <div class="hero-photo" role="img" aria-label="Foto: lächelnde Ärztin mit Stethoskop vor einem Team von Klinikpersonal im Krankenhausflur"></div>
  <header class="title-band">
    <h1>Warum qualifiziertes Personal aus der Türkei?</h1>
    <h2>Unser Angebot – Ihre Vorteile</h2>
  </header>

  <svg class="hub" viewBox="0 0 573 810" aria-hidden="true">
    <circle cx="290" cy="595" r="88" fill="none" stroke="#8fa9a3" stroke-width="1" stroke-dasharray="2 3"/>
    <g fill="none" stroke="#8fa9a3" stroke-width="1" stroke-dasharray="2 3">
      <polyline points="232,487 260,487 280,512"/>
      <polyline points="350,460 320,460 305,508"/>
      <polyline points="232,590 202,590"/>
      <polyline points="378,560 350,560"/>
      <polyline points="240,690 275,690 300,676"/>
      <polyline points="375,660 335,660 318,678"/>
    </g>
    <g fill="#f4f5f4" stroke="var(--teal-dark)" stroke-width="1.5">
      <circle cx="274" cy="510" r="6"/><circle cx="308" cy="508" r="6"/>
      <circle cx="202" cy="590" r="6" stroke="#a9c8bc"/><circle cx="378" cy="560" r="6" stroke="#a9c8bc"/>
      <circle cx="285" cy="682" r="6"/><circle cx="318" cy="678" r="6"/>
    </g>
  </svg>
  <div class="hub-core">Veridan</div>

  <article class="pill pill--left pill--dark" style="left:14px;top:455px">
    <div class="pill__icon"><svg width="22" height="26" viewBox="0 0 22 26"><path d="M11 1C5.5 1 2 5 2 9.5 2 16 11 25 11 25s9-9 9-15.5C20 5 16.5 1 11 1z" fill="var(--teal-dark)"/><circle cx="11" cy="9.5" r="3.5" fill="#fff"/></svg></div>
    <div class="pill__body"><h3>Geografische &amp; politische Nähe</h3><p>Lorem ipsum dolor sit amet, graecequidameoste, facete-diceretvituperatoribusest at.</p></div>
  </article>
  <article class="pill pill--left pill--faint" style="left:14px;top:555px">
    <div class="pill__icon"><svg width="26" height="18" viewBox="0 0 26 18"><path d="M2 8l6-5 5 3 5-3 6 5-8 7-5-3z" fill="none" stroke="#a9c8bc" stroke-width="1.6" stroke-linejoin="round"/></svg></div>
    <div class="pill__body"><h3>Kulturelle Akzeptanz</h3><p>Lorem ipsum dolor sit amet, graecequidameoste, facete-diceretvituperatoribusest at.</p></div>
  </article>
  <article class="pill pill--left pill--mid" style="left:14px;top:655px">
    <div class="pill__icon"><svg width="24" height="24" viewBox="0 0 24 24"><rect x="2" y="2" width="20" height="20" rx="2" fill="none" stroke="var(--teal-mid)" stroke-width="1.8"/><path d="M12 2v20M2 12h20" stroke="var(--teal-mid)" stroke-width="1.8"/></svg></div>
    <div class="pill__body"><h3>Leichtere Integration</h3><p>Lorem ipsum dolor sit amet, graecequidameoste, facetedic-eretvituperatoribusest at.</p></div>
  </article>

  <article class="pill pill--dark" style="left:340px;top:428px">
    <div class="pill__icon"><svg width="26" height="22" viewBox="0 0 26 22"><rect x="2" y="2" width="16" height="12" fill="none" stroke="var(--teal-dark)" stroke-width="1.6"/><circle cx="21" cy="12" r="3" fill="var(--teal-dark)"/><path d="M16 21c0-3 2-5 5-5s4 2 4 5z" fill="var(--teal-dark)"/></svg></div>
    <div class="pill__body"><h3>Hohe Ausbildungsqualität</h3><p>Lorem ipsum dolor sit amet, graecequidameoste, facetedic-eretvituperatoribusest at.</p></div>
  </article>
  <article class="pill pill--faint" style="left:345px;top:525px">
    <div class="pill__icon"><svg width="24" height="24" viewBox="0 0 24 24"><circle cx="8" cy="5" r="3" fill="#a9c8bc"/><circle cx="17" cy="6" r="3" fill="#a9c8bc"/><path d="M4 22v-9h8v9M13 22v-8h8v8" fill="none" stroke="#a9c8bc" stroke-width="1.8"/></svg></div>
    <div class="pill__body"><h3>Gleichwertiges Gesundheitssystem</h3><p>Lorem ipsum dolor sit amet, graecequidameoste, facetedic-eretvituperatoribusest at.</p></div>
  </article>
  <article class="pill pill--mid" style="left:350px;top:625px">
    <div class="pill__icon"><svg width="24" height="24" viewBox="0 0 24 24"><circle cx="10" cy="6" r="4" fill="none" stroke="var(--teal-mid)" stroke-width="1.8"/><path d="M3 22c0-5 3-8 7-8" fill="none" stroke="var(--teal-mid)" stroke-width="1.8"/><path d="M17 13l1.6 3.2 3.4.5-2.5 2.4.6 3.4-3.1-1.6-3.1 1.6.6-3.4-2.5-2.4 3.4-.5z" fill="var(--teal-mid)"/></svg></div>
    <div class="pill__body"><h3>Qualifiziert &amp; motiviert</h3><p>Lorem ipsum dolor sit amet, graecequidameoste, facetedic-eretvituperatoribusest at.</p></div>
  </article>

  <footer class="footer"><span>+49 000 555 01 23</span><span>hr@veridan.example</span><span>www.veridan-hr.example</span></footer>
</section>

<section class="page page--right">
  <h2 class="benefits-title">Genießen Sie weitere Vorteile, wenn Sie uns mit der Rekrutierung neuer Fachkräfte beauftragen.</h2>

  <svg class="brand-hex" viewBox="0 0 190 200" aria-hidden="true"><polygon points="95,8 178,54 178,146 95,192 12,146 12,54" fill="var(--paper)" stroke="var(--teal-dark)" stroke-width="9" stroke-linejoin="round"/></svg>
  <div class="brand-name">Veridan HR</div>

  <svg width="0" height="0" style="position:absolute"><defs><symbol id="hex" viewBox="0 0 34 38"><polygon points="17,1 33,10 33,28 17,37 1,28 1,10" fill="var(--teal-dark)"/></symbol></defs></svg>

  <article class="benefit benefit--l" style="left:30px;top:140px">
    <svg class="benefit__hex"><use href="#hex"/><circle cx="13" cy="17" r="3" fill="none" stroke="#fff" stroke-width="1.4"/><circle cx="21" cy="17" r="3" fill="none" stroke="#fff" stroke-width="1.4"/><path d="M8 26c0-3 2-5 5-5s5 2 5 5M16 26c0-3 2-5 5-5s5 2 5 5" fill="none" stroke="#fff" stroke-width="1.4"/></svg>
    <h4>Vergrößerter Kreis potenzieller Bewerber:innen</h4>
    <p>Lorem ipsum dolor sit amet, consectetur adipiscing elit, sed do eiusmod tempor incididunt ut labore et dolore magna aliqua. Ut enim ad minim veniam.ea commodo consequat.</p>
  </article>
  <article class="benefit benefit--l" style="left:30px;top:262px">
    <svg class="benefit__hex"><use href="#hex"/><circle cx="17" cy="19" r="8" fill="none" stroke="#fff" stroke-width="1.4"/><path d="M17 14v5h4" fill="none" stroke="#fff" stroke-width="1.4"/></svg>
    <h4>Hohe Zeit- und Aufwandersparnis</h4>
    <p>Lorem ipsum dolor sit amet, consectetur adipiscing elit, sed do eiusmod tempor incididunt ut labore et dolore magna aliqua. Ut enim ad minim veniam.ea commodo consequat.</p>
  </article>
  <article class="benefit benefit--l" style="left:30px;top:395px">
    <svg class="benefit__hex"><use href="#hex"/><path d="M10 27l3-7 8-8 4-1-1 4-8 8z" fill="#fff"/></svg>
    <h4>Gesteigerte Innovationskraft</h4>
    <p>Lorem ipsum dolor sit amet, consectetur adipiscing elit, sed do eiusmod tempor incididunt ut labore et dolore magna aliqua. Ut enim ad minim veniam.</p>
  </article>
  <article class="benefit benefit--l" style="left:95px;top:520px;width:200px">
    <svg class="benefit__hex"><use href="#hex"/><circle cx="17" cy="19" r="8" fill="none" stroke="#fff" stroke-width="1.4"/><path d="M9 19h16M17 11c-3 3-3 13 0 16M17 11c3 3 3 13 0 16" fill="none" stroke="#fff" stroke-width="1.2"/></svg>
    <h4>Gesteigerte Internationalisierung</h4>
    <p>Lorem ipsum dolor sit amet, consectetur adipiscing elit, sed do eiusmod tempor incididunt ut labore et dolore magna aliqua. Ut enim ad minim veniam.</p>
  </article>

  <article class="benefit benefit--r" style="left:355px;top:120px">
    <svg class="benefit__hex"><use href="#hex"/><circle cx="16" cy="20" r="6" fill="none" stroke="#fff" stroke-width="1.4"/><path d="M22 10v6M19 13h6" stroke="#fff" stroke-width="1.6"/></svg>
    <h4>Verbesserte Patientenorientierung</h4>
    <p>Lorem ipsum dolor sit amet, consectetur adipiscing elit, sed do eiusmod tempor incididunt ut labore et dolore magna aliqua. Ut enim ad minim veniam.ea commodo consequat.</p>
  </article>
  <article class="benefit benefit--r" style="left:365px;top:232px">
    <svg class="benefit__hex"><use href="#hex"/><circle cx="17" cy="14" r="3" fill="#fff"/><path d="M12 12l5 5 5-5M17 17v9M13 28h8" fill="none" stroke="#fff" stroke-width="1.6"/></svg>
    <h4>Nachhaltiger Erfolg</h4>
    <p>Lorem ipsum dolor sit amet, consectetur adipiscing elit, sed do eiusmod tempor incididunt ut labore et dolore magna aliqua. Ut enim ad minim veniam.ea commodo consequat.</p>
  </article>
  <article class="benefit benefit--r" style="left:372px;top:355px">
    <svg class="benefit__hex"><use href="#hex"/><circle cx="17" cy="15" r="3.5" fill="#fff"/><path d="M11 25c0-4 3-6 6-6s6 2 6 6z" fill="#fff"/></svg>
    <h4>Motivierte Mitarbeiter:innen</h4>
    <p>Lorem ipsum dolor sit amet, consectetur adipiscing elit, sed do eiusmod tempor incididunt ut labore et dolore magna aliqua. Ut enim ad minim veniam.</p>
  </article>
  <article class="benefit benefit--r" style="left:368px;top:472px">
    <svg class="benefit__hex"><use href="#hex"/><path d="M10 27h14M12 27v-5M17 27v-8M22 27v-11" stroke="#fff" stroke-width="2"/></svg>
    <h4>Verbessertes Unternehmensimage</h4>
    <p>Lorem ipsum dolor sit amet, consectetur adipiscing elit, sed do eiusmod tempor incididunt ut labore et dolore magna aliqua. Ut enim ad minim veniam.</p>
  </article>
  <article class="benefit benefit--t" style="left:315px;top:628px;width:210px;text-align:center;padding:24px 14px 12px">
    <svg class="benefit__hex"><use href="#hex"/><path d="M11 13h5v5h-5zM18 13h5v5h-5zM11 20h5v5h-5zM18 20h5v5h-5z" fill="none" stroke="#fff" stroke-width="1.4"/></svg>
    <h4>Gestärkte Vielfalt</h4>
    <p>Lorem ipsum dolor sit amet, consectetur adipiscing elit, sed do eiusmod tempor incididunt ut labore et dolore magna aliqua. Ut enim ad minim veniam.</p>
  </article>

  <footer class="footer"><span>+49 000 555 01 23</span><span>hr@veridan.example</span><span>www.veridan-hr.example</span></footer>
</section>

</body>
</html>
```